Poster design for "A Frame" Sign

I need a design for an A Frame sign. Measurements and Specifications here:
http://www.trimboxdepot.com.au/pg/a-boards/ABPBBLKPRT-Print-Specs.pdf

Actually, it will need to be two designs, one with an arrow pointing left and one with an arrow pointing right, otherwise exactly the same.

LOGO to be used is attached. Colours of design should match logo and should also include orange tones.

The A Frame sign is to be put on the driveway of my home studio at a main road in a residential suburban area. Cars drive by at around 50 km/h, so there needs to be an eye catcher that there is a nurturing home massage studio here.

Logo can be left or right, somehow incorporated into the text below:
-
[Big header, ideally "LeHavre" font]
Sorela Healing
Massage Studio

[slightly smaller font, serif, with bullet points]
- Relaxation Massage
- Remedial Massage
- Pregnancy Massage
- Kahuna Massage

[big Arrow to the left/right - one for each side of the frame]

[sans serif font, same size as above]
Bookings essential!
ph 0491 578 264
www.sorelahealing.com.au

[serif font, same as above]
EFTPOS and instant health fund claims available.
-

Residential

f37022

```html
<!DOCTYPE html>
<html lang="en">
<head>
<meta charset="utf-8">
<title>Sorela Healing Massage – A Frame Sign</title>
<link href="https://fonts.googleapis.com/css2?family=Federo&family=Questrial&display=swap" rel="stylesheet">
<style>
  :root {
    --bg-light: #ffffff;
    --bg-edge: #d9d9db;
    --maroon: #8c1c3e;
    --pink: #e0186c;
    --pink-soft: #ef6fa5;
    --white: #ffffff;
  }
  * { margin: 0; padding: 0; box-sizing: border-box; }
  html, body { width: 811px; height: 1200px; overflow: hidden; }
  body { background: var(--bg-edge); }
  .sign {
    position: relative;
    width: 811px;
    height: 1200px;
    overflow: hidden;
    background: radial-gradient(ellipse at 50% 45%, var(--bg-light) 0%, #f1f1f2 55%, var(--bg-edge) 100%);
    font-family: "Questrial", sans-serif;
    text-align: center;
  }
  .brand-mark {
    position: absolute;
    left: 260px; top: 20px;
    width: 292px; height: 292px;
    border-radius: 50%;
    background: var(--pink);
    display: flex; align-items: center; justify-content: center;
    color: var(--white);
    font-family: "Questrial", sans-serif;
    font-size: 40px;
  }
  .headline {
    position: absolute;
    left: 0; right: 0; top: 390px;
    font-family: "Federo", sans-serif;
    color: var(--maroon);
    line-height: 1;
    text-transform: uppercase;
  }
  .headline .name { display: block; font-size: 76px; letter-spacing: 1px; }
  .headline .trade { display: block; font-size: 80px; margin-top: 4px; letter-spacing: 3px; }
  .services {
    position: absolute;
    left: 0; right: 0; top: 562px;
    list-style: none;
    color: var(--pink);
    font-size: 37px;
    line-height: 45px;
  }
  .booking-arrow { position: absolute; left: 59px; top: 785px; width: 624px; height: 122px; }
  .booking-text {
    position: absolute; left: 110px; top: 788px; width: 570px;
    color: var(--white);
  }
  .booking-text .phone { display: block; font-size: 82px; line-height: 80px; letter-spacing: 2px; }
  .booking-text .note { display: block; font-size: 32px; line-height: 36px; letter-spacing: 1px; }
  .web {
    position: absolute; left: 0; right: 0; top: 926px;
    color: var(--maroon); font-size: 40px; line-height: 48px; letter-spacing: 1px;
  }
  .payments {
    position: absolute; left: 0; right: 0; top: 976px;
    color: var(--maroon); font-size: 26px; line-height: 30px;
  }
  .swoosh { position: absolute; left: 0; bottom: 0; width: 811px; height: 170px; }
</style>
</head>
<body>
  <main class="sign">
    <div class="brand-mark">Sorela</div>

    <h1 class="headline">
      <span class="name">Sorela Healing</span>
      <span class="trade">Massage</span>
    </h1>

    <ul class="services">
      <li>Relaxation Massage</li>
      <li>Remedial Massage</li>
      <li>Pregnancy Massage</li>
      <li>Kahuna Massage</li>
    </ul>

    <svg class="booking-arrow" viewBox="0 0 624 122" aria-hidden="true">
      <polygon points="0,61 52,0 624,0 624,122 52,122" fill="var(--pink)"/>
    </svg>
    <p class="booking-text">
      <span class="phone">0491 578 264</span>
      <span class="note">Bookings essential!</span>
    </p>

    <p class="web">www.sorelahealing.com.au</p>
    <p class="payments">EFTPOS and instant health fund claims available.</p>

    <svg class="swoosh" viewBox="0 0 811 170" preserveAspectRatio="none" aria-hidden="true">
      <path d="M0,55 C260,10 540,10 811,50 L811,170 L0,170 Z" fill="var(--pink-soft)"/>
      <path d="M0,95 C260,45 540,45 811,85 L811,170 L0,170 Z" fill="var(--pink)"/>
      <path d="M0,140 C280,95 560,95 811,130 L811,170 L0,170 Z" fill="var(--maroon)"/>
    </svg>
  </main>
</body>
</html>
```